Custom unique Stationary design for Logistics company

We need a custom, unique , elegant and luxurious full stationary design using our new logo, following these guidelines:
1- Business card: double sided, both sides uses the navy blue as the background main color (same as the code of the navy blue used in our logo).
2- envelope and folder: also use the same navy blue as the main background color.
3- book cover( notepad cover) : same thing with the navy blue
4- letterhead: feel free to use the combination of the colors in our logo.
5- rest of the items are up to your creativity

Target Market(s)

corporates and other businesses

Industry/Entity Type

Logistics and heavy machines contractors

Requirements
Must have
• Letterhead, business card, envelope, notepad cover, paper, file
Nice to have
• navy blue to be main background color for business card, envelope, notepad cover

```html
<!DOCTYPE html>
<html lang="en">
<head>
<meta charset="utf-8">
<title>Northline Cargo – Business Card</title>
<link rel="stylesheet" href="https://fonts.googleapis.com/css2?family=Karla:wght@400;500;700&family=Rubik:wght@600&display=swap">
<style>
  :root {
    --page-bg: #e9e6e1;
    --card-light: #eef1f4;
    --navy: #0f2744;
    --navy-deep: #0a1b30;
    --red: #c9301d;
    --gap-white: #dfe3e8;
    --name-navy: #1f3a5a;
    --text-grey: #4a5058;
    --logo-light: #d9dde2;
  }
  * { margin: 0; padding: 0; box-sizing: border-box; }
  html, body {
    width: 1200px; height: 969px; overflow: hidden;
    background: var(--page-bg);
  }
  .card {
    position: absolute; left: 100px; top: 200px;
    width: 1000px; height: 569px;
    border-radius: 30px; overflow: hidden;
    background: linear-gradient(160deg, #f6f8fa 0%, var(--card-light) 60%, #e4e8ec 100%);
    box-shadow: 0 10px 30px rgba(0,0,0,0.18);
  }
  .card-shapes { position: absolute; inset: 0; width: 100%; height: 100%; }
  .contact-block {
    position: absolute; left: 74px; top: 152px;
    font-family: "Karla", sans-serif; color: var(--text-grey);
  }
  .holder-name {
    font-family: "Rubik", sans-serif; font-weight: 600;
    font-size: 30px; letter-spacing: 0.3px; color: var(--name-navy);
    line-height: 34px;
  }
  .holder-title {
    font-size: 21px; font-weight: 500; color: var(--red);
    line-height: 28px; margin-bottom: 8px;
  }
  .address { font-size: 21px; line-height: 28px; margin-bottom: 10px; }
  .contact-list { list-style: none; }
  .contact-list li {
    display: flex; align-items: center; gap: 12px;
    font-size: 21px; line-height: 28.5px;
  }
  .contact-list svg { width: 18px; height: 18px; flex: none; fill: var(--red); }
  .brand-name {
    position: absolute; left: 610px; top: 245px; width: 340px;
    text-align: center;
    font-family: "Karla", sans-serif; font-weight: 700;
    font-size: 40px; letter-spacing: 3px; color: var(--logo-light);
  }
</style>
</head>
<body>
  <div class="card">
    <svg class="card-shapes" viewBox="0 0 1000 569" preserveAspectRatio="none" aria-hidden="true">
      <defs>
        <linearGradient id="navyPanel" x1="0" y1="0" x2="1" y2="1">
          <stop offset="0" stop-color="#123057"/>
          <stop offset="1" stop-color="var(--navy-deep)"/>
        </linearGradient>
      </defs>
      <polygon points="695,0 404,289 663,569 1000,569 1000,0" fill="var(--red)"/>
      <polygon points="730,0 438,289 700,569 1000,569 1000,0" fill="var(--gap-white)"/>
      <polygon points="746,0 460,289 738,569 1000,569 1000,0" fill="url(#navyPanel)"/>
    </svg>

    <div class="contact-block">
      <p class="holder-name">DANIEL HARPER</p>
      <p class="holder-title">President</p>
      <p class="address">4120 Juniper Court<br>Fairbanks, Alaska 99701</p>
      <ul class="contact-list">
        <li><svg viewBox="0 0 24 24"><path d="M6.6 10.8a15.1 15.1 0 0 0 6.6 6.6l2.2-2.2a1 1 0 0 1 1-.25 11.4 11.4 0 0 0 3.6.57 1 1 0 0 1 1 1V20a1 1 0 0 1-1 1A17 17 0 0 1 3 4a1 1 0 0 1 1-1h3.5a1 1 0 0 1 1 1c0 1.25.2 2.45.57 3.57a1 1 0 0 1-.25 1z"/></svg>555-204-7318</li>
        <li><svg viewBox="0 0 24 24"><path d="M7 1h10a2 2 0 0 1 2 2v18a2 2 0 0 1-2 2H7a2 2 0 0 1-2-2V3a2 2 0 0 1 2-2zm0 3v14h10V4zm5 15.5a1.2 1.2 0 1 0 0 2.4 1.2 1.2 0 0 0 0-2.4z"/></svg>555-419-6032</li>
        <li><svg viewBox="0 0 24 24"><path d="M2 5h20v14H2zm2 2v.5l8 5 8-5V7zm0 2.8V17h16V9.8l-8 5z"/></svg>daniel@northlinecargo.com</li>
        <li><svg viewBox="0 0 24 24"><circle cx="12" cy="12" r="10"/></svg>www.northlinecargo.com</li>
      </ul>
    </div>

    <p class="brand-name">NORTHLINE CARGO</p>
  </div>
</body>
</html>
```